Exclusive beauty salon needs a price list or services booklet

I need a new very attractive flyer for my beauty salon, containing information on the different services and their prices.
In attachment you can find a pdf of the "old" one, but I'd love to have a beautifully designed new one!
I'd love to have a booklet in format 148 x 148 mm, or in US format, containing 12 or 16 pages, but if you can offer other nice looking designs they are welcome!
The services that need to come in the booklet with their prices can all be found on my website: www.atelierverano.be, starting with
Gelaatsverzorging
Wimperverlenging
Suikerontharing
Wimperlifting
Permanente Make Up
Airbrush Tanning

Target Market(s)

woman from 20 to 89 years old

Industry/Entity Type

Beauty Salon

Font styles to use
Sans Serif

Colors

Designer to choose colors to be used in the design.

Requirements
Must have
• a classy nice look, it must contain details about the services from my beauty salon and their prices, and nice pictures.
• The Names, prices and explanations of the services can easily be found on my website: www.atelierverano.be
Nice to have
• In attachment you can find the "old" price list in pdf, what I need now is a "new booklet" with the new logo and updated services price list.
• I need a very nice and attractive looking booklet, classy chique, Paris chique, looking very expensive.
Should not have
• Not too much colors, not too curly, but still feminine

```html
<!DOCTYPE html>
<html lang="nl">
<head>
<meta charset="utf-8">
<title>Prijslijst Permanente Make Up</title>
<link href="https://fonts.googleapis.com/css2?family=Prata&family=Poppins:wght@300;400&display=swap" rel="stylesheet">
<style>
  :root {
    --bg: #d9d9d9;
    --page: #ffffff;
    --teal: #8ccfca;
    --teal-band: #a3dad5;
    --teal-dark: #6fbcb6;
    --ink: #3a3a3a;
    --gutter: rgba(0,0,0,0.08);
  }
  * { box-sizing: border-box; margin: 0; padding: 0; }
  html, body { width: 1200px; height: 900px; overflow: hidden; }
  body {
    background: var(--bg);
    font-family: "Poppins", sans-serif;
    font-weight: 300;
    color: var(--ink);
    position: relative;
  }
  .spread {
    position: absolute;
    left: 40px; top: 165px;
    width: 1120px; height: 570px;
    display: flex;
    box-shadow: 0 4px 14px rgba(0,0,0,0.18);
  }
  .page {
    position: relative;
    width: 560px; height: 570px;
    background: var(--page);
    overflow: hidden;
  }
  .page--left { background: linear-gradient(to left, var(--gutter), transparent 30px), var(--page); }
  .page--right { background: linear-gradient(to right, var(--gutter), transparent 30px), var(--page); }

  .photo {
    position: absolute;
    width: 122px; height: 122px;
    border-radius: 50%;
  }
  .photo--lips { background: radial-gradient(circle at 50% 50%, #c2303a, #e9b3a6 75%); }
  .photo--eye-smoky { background: radial-gradient(circle at 50% 50%, #3b4a55, #c9a590 70%); }
  .photo--eye-wing { background: radial-gradient(circle at 50% 55%, #3a2e2a, #e4c8b6 60%); }
  .photo--lashes { background: radial-gradient(circle at 50% 55%, #6b4a33, #e6d2c4 65%); }

  .service { position: absolute; }
  .service__title {
    font-family: "Prata", serif;
    font-weight: 400;
    color: var(--teal-dark);
    font-size: 12.5px;
    line-height: 1.35;
    margin-bottom: 6px;
  }
  .service__text { font-size: 8.5px; line-height: 1.6; }
  .service__list { list-style: none; font-size: 8.5px; line-height: 1.6; }
  .service__list--indent { padding-left: 18px; }
  .service__list li::before { content: "• "; }
  .price {
    display: inline-block;
    background: var(--teal);
    color: #fff;
    font-size: 9px;
    padding: 2px 7px;
    margin-top: 8px;
  }
  .price--brow { position: absolute; top: 404px; margin: 0; }
  .band {
    position: absolute;
    left: 0; top: 438px;
    width: 560px; height: 132px;
    background: linear-gradient(100deg, var(--teal-band), #9ad5cf);
  }
  .band .service__title { color: #2f4f4d; margin-bottom: 4px; }
  .band .price { background: #7fc6c0; margin: 0 0 4px; }
  .band__label { font-size: 8.5px; font-weight: 400; line-height: 1.6; }
</style>
</head>
<body>
  <div class="spread">
    <section class="page page--left">
      <div class="photo photo--lips" role="img" aria-label="Foto van volle rode lippen" style="left:50px; top:40px;"></div>
      <div class="service" style="left:213px; top:30px; width:320px;">
        <h2 class="service__title">Full lips</h2>
        <p class="service__text">Een kleuraccent aan uw mond</p>
        <ul class="service__list service__list--indent">
          <li>Uw herstelde lijnen preciseert uw natuurlijke mond</li>
          <li>Een schaduweffect waarbij de lijn uitschaduwt op de mond</li>
          <li>Full lips vervolledigt de natuurlijke lipkleur</li>
          <li>Camoufleert oneffenheden zoals pigmentvlekjes, hypopigmentatie</li>
          <li>Vergroot boven en/ of onderlip</li>
          <li>Full lips kleurt de mond volledig</li>
        </ul>
        <span class="price">€ 595</span>
      </div>

      <div class="photo photo--eye-smoky" role="img" aria-label="Foto van een oog met volledige oogcontour" style="left:50px; top:224px;"></div>
      <div class="service" style="left:213px; top:214px; width:320px;">
        <h2 class="service__title">Permanente make up volledige oogcontour</h2>
        <p class="service__text">Je tekent al jarenlang een lijntje boven en onder uw oog?<br>Een perfecte vorm is nodig want dit vervangt wel degelijk uw make-up! Ik ben altijd eerlijk en oprecht want uw mooie liner is mijn beste reclame! Ik geef heel graag advies over de mogelijkheden.<br>Alles wordt uitvoerig besproken en uitgetekend zo ziet u al hoe uw eyeliner er zal uitzien en kan u zelf aangeven of u deze liner of net iets dikker wenst.</p>
        <span class="price">€ 360</span>
      </div>

      <div class="photo photo--eye-wing" role="img" aria-label="Foto van een oog met brede eyeliner" style="left:50px; top:404px;"></div>
      <div class="service" style="left:213px; top:394px; width:320px;">
        <h2 class="service__title">Brede eyeliner boven het oog</h2>
        <p class="service__text">Je tekent al jarenlang een "dikker" lijntje ?<br>Een perfecte vorm is nodig want dit vervangt wel degelijk uw make-up! Ik ben altijd eerlijk en oprecht want uw mooie liner is mijn beste reclame! Ik geef heel graag advies over de mogelijkheden.<br>Alles wordt uitvoerig besproken en uitgetekend zo ziet u al hoe uw eyeliner er zal uitzien en kan u zelf aangeven of u deze liner of net iets dikker wenst.</p>
        <span class="price">€ 235</span>
      </div>
    </section>

    <section class="page page--right">
      <div class="photo photo--lashes" role="img" aria-label="Foto van een oog met wimperinvulling" style="left:54px; top:36px;"></div>
      <div class="service" style="left:202px; top:32px; width:330px;">
        <h2 class="service__title">Fijne eyeliner boven (wimperinvulling) het oog</h2>
        <p class="service__text">De fijne eyeliner of wimperinvulling om uw ogen op een subtiele manier iets meer accentueren en laten spreken!<br>Een eye-liner met subtiele klasse!</p>
        <ul class="service__list service__list--indent">
          <li>uw ogen zullen meer spreken en u hoeft zich geen zorgen meer te maken over uitgelopen lijntjes of panda ogen.</li>
          <li>een echte liner zonder het too much effect.</li>
        </ul>
        <span class="price">€186</span>
      </div>

      <div class="service" style="left:52px; top:196px; width:230px;">
        <h2 class="service__title">Wenkbrauwen Hairstroke<br>Techniek</h2>
        <p class="service__text">Voor wie?</p>
        <ul class="service__list">
          <li>je wenst een hyper realistisch natuurlijk resultaat</li>
          <li>je hebt weinig tot geen eigen haartjes</li>
          <li>je bent het niet gewend om make up op je wenkbrauwen te gebruiken</li>
        </ul>
        <p class="service__text">Oplossing</p>
        <ul class="service__list">
          <li>er worden hairstrokes (fijne haartjes) gepigmenteerd op de huid</li>
          <li>voor een vollere wenkbrauw</li>
          <li>met een heel natuurlijke look</li>
        </ul>
      </div>
      <span class="price price--brow" style="left:52px;">€ 320</span>

      <div class="service" style="left:308px; top:196px; width:225px;">
        <h2 class="service__title">Wenkbrauwen Shading Brow<br>of Poederwenkbrauw</h2>
        <p class="service__text">Voor wie?</p>
        <ul class="service__list">
          <li>je wil elke dag mooi gevormde wenkbrauwen</li>
          <li>je houdt van de soft make up look</li>
          <li>je hebt weinig tot voldoende eigen haartjes</li>
        </ul>
        <p class="service__text">Oplossing:</p>
        <ul class="service__list">
          <li>intensere kleur geven aan de wenkbrauw</li>
          <li>mooie vorm geven aan de wenkbrauw</li>
          <li>voor een mooie, zachte make up look gezien bij Lena Marsh</li>
        </ul>
      </div>
      <span class="price price--brow" style="left:308px;">€ 320</span>

      <div class="band">
        <div class="service" style="left:50px; top:10px; width:240px;">
          <h2 class="service__title">Wenkbrauwen Power Brow</h2>
          <span class="price">€ 320</span>
          <p class="band__label">voor wie:</p>
          <ul class="service__list">
            <li>je wenst een meer uitgesproken resultaat</li>
            <li>je draagt dagelijks make up aan de wenkbrauwen</li>
            <li>je hebt voldoende haartjes</li>
          </ul>
        </div>
        <div class="service" style="left:300px; top:14px; width:240px;">
          <p class="band__label">oplossing:</p>
          <ul class="service__list">
            <li>shading techniek + hairstroke techniek = power brow</li>
            <li>voller maken van de eigen wenkbrauw</li>
            <li>meer kleur en vorm geven</li>
            <li>voor de echte make up look</li>
          </ul>
          <p class="service__text">Gezien bij Nora Vale</p>
        </div>
      </div>
    </section>
  </div>
</body>
</html>
```